Business Intelligence Application - Reporting Menu and Report Criteria Design

Looking for a fresh, effective and user friendly view for the menu structure and reporting criteria screen format for a business reporting application. Initial format completed, content structure is in place, but we need the 'wow' design.. as its a serious professional report/BI tool it has to fall within certain guidelines for clarity and graphics..but we want it to be slick, friendly, great user experience. There is a large amount of complex content to fit into a small space and we need it to be very inviting, modern and intuitive.. If interested, please review the attachment. We have live screens in operation, but feel these could be improved and looking forward to seeing what great creative suggestions could be made. Please review work done to date in the attached.. We are not looking for a total re-design of everything, all the basic business content/structure is there.. but tell us what we could do to improve this in terms of graphic design... particularly the criteria screens.. thanks!
Updates

Reason: Need a few more days to review designs - thanks for all submissions so far, we will make a selection shortly.

Target Market(s)

Business analysts, hotel operations teams, finance analysts hospitality industry

Industry/Entity Type

Hospitality

Coding

Coded - Design and coding required

Number of Pages Required

4 page

Font styles to use
Sans Serif
Other font styles liked:
• Candara, please see example in deck

Colors
3276b5
3176b5
0255a3
85acd3
33a6d7
cee9f5
85cae6

Requirements
Must have
• sharp clear, logical menu structure, (currently it has 'clicks to sub-menus, we need hover over, slide to sub-menus..) colour, styling.. and most focus on revision of criteria.. right now is somewhat heavy, cumbersome.. keep colour and friendly intuitive process steps.. its heavy analytical stuff.. best of luck!
Should not have
• No grey fonts on white or grey screens! many business apps are not readable or sharp.. or fonts are too small.. colourless, so please avoid that.. see our deck - sharp dark (navy) or black fonts on white, or light shading..

```html
<!DOCTYPE html>
<html lang="en">
<head>
<meta charset="utf-8">
<title>RateView – Property Search</title>
<link href="https://fonts.googleapis.com/css2?family=Mulish:wght@400;600;700&display=swap" rel="stylesheet">
<style>
  :root{
    --header-bg:#021a35;
    --nav-bg:#0a4282;
    --nav-active:#2d6f93;
    --nav-text:#b7c3d1;
    --nav-divider:#2a5c96;
    --stage-top:#1d6b88;
    --stage-bottom:#02284f;
    --panel-top:#f7f8f8;
    --panel-bottom:#d9d9d9;
    --panel-shade:#2b7a95;
    --title:#1259ad;
    --item:#0b2e6e;
    --bullet:#2c8fd6;
    --brand:#17a394;
    --welcome:#8a96a3;
    --footer-bg:#6e6e6e;
    --footer-text:#121212;
    --page-active-top:#0a62b8;
    --page-active-bottom:#023e86;
  }
  *{box-sizing:border-box;margin:0;padding:0}
  html,body{width:1200px;height:664px;overflow:hidden}
  body{font-family:"Mulish",sans-serif;position:relative;background:var(--stage-bottom)}

  .app-header{position:absolute;left:0;top:0;width:1200px;height:113px;background:var(--header-bg)}
  .brand{position:absolute;left:99px;top:43px;display:flex;align-items:center;gap:12px}
  .brand-mark{width:32px;height:32px;border-radius:50%;background:var(--brand)}
  .brand-name{font-size:26px;font-weight:700;color:var(--brand);letter-spacing:.2px}
  .user-avatar{position:absolute;left:781px;top:34px;width:44px;height:44px;border-radius:50%;background:radial-gradient(circle at 50% 40%,#b9a796,#5a4d44)}
  .user-greeting{position:absolute;left:833px;top:37px;font-size:15px;line-height:21px;color:var(--welcome)}
  .header-divider{position:absolute;top:40px;width:1px;height:38px;background:#0d2a48}
  .header-icon{position:absolute;top:44px}

  .main-nav{position:absolute;left:0;top:113px;width:1200px;height:51px;background:var(--nav-bg)}
  .main-nav ul{list-style:none;display:flex;position:absolute;left:137px;top:0;height:51px}
  .main-nav li{height:51px;display:flex;align-items:center;justify-content:center;border-left:1px solid var(--nav-divider);font-size:13px;font-weight:700;color:var(--nav-text);white-space:nowrap;gap:4px}
  .main-nav li.is-active{background:var(--nav-active)}
  .nav-badge{width:20px;height:20px;border-radius:50%;background:#b07a3c}

  .stage{position:absolute;left:0;top:164px;width:1200px;height:425px;background:linear-gradient(170deg,var(--stage-top) 0%,#0d4a70 45%,var(--stage-bottom) 100%)}
  .panel-shadow{position:absolute;left:112px;top:19px;width:40px;height:320px;background:var(--panel-shade);opacity:.7}
  .results-panel{position:absolute;left:142px;top:8px;width:945px;height:331px;background:linear-gradient(180deg,var(--panel-top),var(--panel-bottom))}
  .results-title{position:absolute;left:50px;top:37px;font-size:19px;font-weight:700;color:var(--title);letter-spacing:.2px}
  .results-list{list-style:none;position:absolute;left:52px;top:87px;width:880px;display:grid;grid-template-columns:228px 239px 228px 185px;grid-auto-flow:column;grid-template-rows:repeat(5,32.6px)}
  .results-list li{font-size:15px;color:var(--item);display:flex;align-items:center;gap:7px;white-space:nowrap}
  .results-list li::before{content:"";border-left:5px solid var(--bullet);border-top:5px solid transparent;border-bottom:5px solid transparent}
  .pagination{position:absolute;left:316px;top:280px;display:flex;gap:4px}
  .page-btn{width:32px;height:31px;border:1px solid #c4c4c4;background:linear-gradient(#f6f6f6,#e2e2e2);font-size:14px;font-weight:600;color:#333;display:flex;align-items:center;justify-content:center}
  .page-btn.is-current{background:linear-gradient(var(--page-active-top),var(--page-active-bottom));color:#fff;border-color:#02407f}

  .app-footer{position:absolute;left:0;top:589px;width:1200px;height:75px;background:var(--footer-bg);text-align:center;font-size:13.5px;color:var(--footer-text);padding-top:24px;word-spacing:1px}
</style>
</head>
<body>
  <header class="app-header">
    <div class="brand"><span class="brand-mark"></span><span class="brand-name">RateView</span></div>
    <div class="user-avatar" role="img" aria-label="Profile photo of the signed-in administrator"></div>
    <div class="user-greeting">Welcome<br>Admin</div>
    <span class="header-divider" style="left:919px"></span>
    <svg class="header-icon" style="left:946px" width="28" height="28" viewBox="0 0 24 24" aria-label="Notifications"><path fill="#1b6fc2" d="M12 2a1.6 1.6 0 0 1 1.6 1.6v.6A6.5 6.5 0 0 1 18.5 10.5v4.8L20.5 18v1H3.5v-1l2-2.7v-4.8A6.5 6.5 0 0 1 10.4 4.2v-.6A1.6 1.6 0 0 1 12 2zm-2.3 18h4.6a2.3 2.3 0 0 1-4.6 0z"/></svg>
    <span class="header-divider" style="left:1004px"></span>
    <svg class="header-icon" style="left:1035px" width="30" height="26" viewBox="0 0 30 26" aria-label="Share"><path fill="#1b6fc2" d="M18 2l10 9-10 9v-5.5C11 14.5 6 16.5 2 23c1-8 6-14 16-15.5z"/></svg>
  </header>

  <nav class="main-nav">
    <ul>
      <li style="width:100px">Management</li>
      <li style="width:144px">Rooms Performance</li>
      <li style="width:134px">Revenue Summary</li>
      <li style="width:111px">Demand &amp; Risk</li>
      <li style="width:133px">Inventory Analysis</li>
      <li style="width:89px">Placeholder</li>
      <li class="is-active" style="width:141px"><span class="nav-badge" role="img" aria-label="Property search mascot icon"></span>Property Search</li>
      <li style="width:43px">Intel</li>
      <li style="width:71px">Planning</li>
    </ul>
  </nav>

  <main class="stage">
    <div class="panel-shadow"></div>
    <section class="results-panel">
      <h1 class="results-title">SEARCH RESULT</h1>
      <ul class="results-list">
        <li>Marlowe Hotel</li>
        <li>Grand Marlowe Hotel</li>
        <li>Riverside Arch Hotel</li>
        <li>Central Quay Hotel</li>
        <li>Sociosqu ad litora</li>
        <li>Torquent per</li>
        <li>Conubia nostra</li>
        <li>Per inceptos hymenaeos</li>
        <li>Donec quis mi sed</li>
        <li>Aagna hendrerit</li>
        <li>Suspendisse risus nibh</li>
        <li>Nltricies eu volutpat</li>
        <li>Non condimentum</li>
        <li>Pendrerit augue</li>
        <li>Etiam eleifend</li>
        <li>Metus vitae</li>
        <li>Adipiscing semper</li>
        <li>Pauris ipsum iaculis</li>
        <li>Elit congue</li>
        <li>Gravida elit mi</li>
      </ul>
      <div class="pagination">
        <span class="page-btn"><svg width="10" height="14" viewBox="0 0 10 14"><path d="M8 1L2 7l6 6" fill="none" stroke="#555" stroke-width="1.6"/></svg></span>
        <span class="page-btn is-current">1</span>
        <span class="page-btn">2</span>
        <span class="page-btn">3</span>
        <span class="page-btn">4</span>
        <span class="page-btn">5</span>
        <span class="page-btn"><svg width="10" height="14" viewBox="0 0 10 14"><path d="M2 1l6 6-6 6" fill="none" stroke="#555" stroke-width="1.6"/></svg></span>
      </div>
    </section>
  </main>

  <footer class="app-footer">© 2017 Company Name&nbsp; All right reserved&nbsp; Term of Use</footer>
</body>
</html>
```